Construction Company Cellar Crafters needs Business Card

I would like modern looking business card design. I am attaching logo of our company. Please include cell nr 302.418.7650 , email address cellarcrafters4u@examplemail.com, web : cellarcrafters4u.com, please also include wording: Specializing in finishing and remodeling basements. You can play with dark grey and orange colors or any ideas are welcome. Also include social media icons Friendloop and HouseGuidr.

```html
<!DOCTYPE html>
<html lang="en">
<head>
<meta charset="utf-8">
<title>Cellar Crafters – Business Card</title>
<link href="https://fonts.googleapis.com/css2?family=Open+Sans:wght@400;600;700&display=swap" rel="stylesheet">
<style>
  :root {
    --orange: #f05a28;
    --ink: #141414;
    --white: #ffffff;
    --page: #ecebe8;
    --shadow: rgba(0,0,0,0.18);
  }
  * { margin: 0; padding: 0; box-sizing: border-box; }
  html, body {
    width: 1200px; height: 900px; overflow: hidden;
    background: var(--page);
    font-family: "Open Sans", sans-serif;
  }
  .canvas { position: relative; width: 1200px; height: 900px; }

  .card {
    position: absolute;
    box-shadow: 0 6px 18px var(--shadow);
    overflow: hidden;
  }

  /* Front */
  .card-front {
    left: 237px; top: 60px; width: 556px; height: 345px;
    background: var(--white);
  }
  .front-brand {
    position: absolute; left: 35px; top: 110px;
    color: var(--orange);
    font-weight: 600; font-size: 34px; letter-spacing: 1px;
    text-transform: uppercase; line-height: 1;
  }
  .front-band {
    position: absolute; left: 0; top: 158px; width: 556px; height: 170px;
    background: var(--orange);
    color: var(--white);
  }
  .person-name {
    position: absolute; left: 34px; top: 10px;
    font-weight: 700; font-size: 18px;
  }
  .person-title {
    position: absolute; left: 34px; top: 32px;
    font-size: 14px;
  }
  .social-row {
    position: absolute; left: 36px; top: 68px;
    display: flex; gap: 14px; font-size: 12px; font-weight: 600;
  }
  .social-item { display: flex; align-items: center; gap: 5px; }
  .social-dot { width: 12px; height: 12px; background: var(--white); }
  .contact-list {
    position: absolute; left: 33px; top: 102px;
    list-style: none; font-size: 14px; line-height: 20.5px;
  }
  .contact-list li { display: flex; align-items: center; gap: 8px; }
  .contact-list svg { width: 11px; height: 11px; fill: var(--white); flex: none; }

  /* Back */
  .card-back {
    left: 457px; top: 518px; width: 560px; height: 344px;
    background: var(--ink);
  }
  .back-brand {
    position: absolute; left: 0; right: 0; top: 150px;
    text-align: center;
    color: var(--orange);
    font-weight: 600; font-size: 42px; letter-spacing: 1px;
    text-transform: uppercase; line-height: 1;
  }
  .tagline {
    position: absolute; left: 0; right: 0; top: 274px;
    text-align: center;
    color: var(--orange);
    font-size: 13px; text-transform: uppercase;
  }
</style>
</head>
<body>
<main class="canvas">

  <section class="card card-front" aria-label="Business card front">
    <div class="front-brand">Cellar Crafters</div>
    <div class="front-band">
      <div class="person-name">Daniel Porter</div>
      <div class="person-title">Managing Director</div>
      <div class="social-row">
        <span class="social-item"><span class="social-dot"></span>Friendloop</span>
        <span class="social-item"><span class="social-dot"></span>HouseGuidr</span>
      </div>
      <ul class="contact-list">
        <li>
          <svg viewBox="0 0 24 24"><path d="M6.6 10.8a15.1 15.1 0 0 0 6.6 6.6l2.2-2.2c.3-.3.7-.4 1-.2 1.1.4 2.3.6 3.6.6.6 0 1 .4 1 1V20c0 .6-.4 1-1 1A17 17 0 0 1 3 4c0-.6.4-1 1-1h3.5c.6 0 1 .4 1 1 0 1.3.2 2.5.6 3.6.1.3 0 .7-.2 1z"/></svg>
          302.418.7650
        </li>
        <li>
          <svg viewBox="0 0 24 24"><path d="M2 5h20v14H2z M2 5l10 8 10-8" fill="none" stroke="#fff" stroke-width="2"/><path d="M3 6l9 7 9-7v12H3z"/></svg>
          cellarcrafters4u@examplemail.com
        </li>
        <li>
          <svg viewBox="0 0 24 24"><circle cx="12" cy="12" r="10"/></svg>
          cellarcrafters4u.com
        </li>
      </ul>
    </div>
  </section>

  <section class="card card-back" aria-label="Business card back">
    <div class="back-brand">Cellar Crafters</div>
    <p class="tagline">Specializing in finishing and remodeling basements.</p>
  </section>

</main>
</body>
</html>
```